MEDICAL CLINIC LETTERHEAD

Design is a letterhead for a non-profit medical center. The name of the clinic is VITARIDGE Community Health Center. Although the full name must be included, the community health center part is more of a description and should be less visible - i attached an example of what I mean by that (ATTACHED IMAGE IS AN EXAMPLE OF FONT SIZES NOT A DESIGN IDEA). Please design something modern, cool looking and unique because I can always download free templates.
Phone, email, website and etc will be added later.

Industry/Entity Type

MEDICAL

```html
<!DOCTYPE html>
<html lang="en">
<head>
<meta charset="utf-8">
<title>VITARIDGE Community Health Center – Letterhead</title>
<link href="https://fonts.googleapis.com/css2?family=Roboto:wght@400;700&family=Questrial&display=swap" rel="stylesheet">
<style>
  :root {
    --navy: #0c2b55;
    --ink: #4d4d4d;
    --muted: #7a7a7a;
    --rule: #c9c9c9;
    --paper: #ffffff;
  }
  * { margin: 0; padding: 0; box-sizing: border-box; }
  html, body { width: 1023px; height: 1200px; overflow: hidden; background: var(--paper); }
  .letterhead {
    position: relative;
    width: 1023px;
    height: 1200px;
    background: var(--paper);
    color: var(--ink);
    font-family: "Questrial", sans-serif;
  }
  .brand {
    position: absolute;
    left: 98px;
    top: 92px;
  }
  .brand-name {
    font-family: "Roboto", sans-serif;
    font-weight: 700;
    font-size: 49px;
    line-height: 1;
    letter-spacing: -0.5px;
    color: var(--navy);
  }
  .brand-tagline {
    font-family: "Roboto", sans-serif;
    font-size: 14.5px;
    letter-spacing: 3.2px;
    color: var(--muted);
    margin-top: 3px;
  }
  .contact {
    position: absolute;
    right: 84px;
    top: 104px;
    display: flex;
    align-items: stretch;
    font-family: "Roboto", sans-serif;
    font-size: 14.5px;
    color: var(--ink);
  }
  .contact-address {
    text-align: right;
    line-height: 18px;
    padding: 6px 16px 0 0;
    border-right: 1px solid var(--rule);
  }
  .contact-lines {
    list-style: none;
    padding-left: 16px;
    line-height: 20px;
  }
  .contact-lines li { display: flex; align-items: center; gap: 8px; }
  .contact-lines svg { width: 12px; height: 12px; fill: var(--navy); flex: none; }
  .letter-body {
    position: absolute;
    left: 98px;
    right: 84px;
    top: 318px;
    font-size: 15.2px;
    line-height: 21.5px;
    text-align: justify;
  }
  .salutation { font-size: 19px; margin-bottom: 38px; text-align: left; }
  .letter-body p { margin-bottom: 21.5px; }
  .letter-body p.gap-before { margin-top: 14px; }
  .closing { margin-top: 64px; text-align: left; }
  .footer-band {
    position: absolute;
    left: 0; right: 0; bottom: 0;
    height: 22px;
    background: var(--navy);
  }
</style>
</head>
<body>
<main class="letterhead">
  <header>
    <div class="brand">
      <div class="brand-name">VITARIDGE</div>
      <div class="brand-tagline">COMMUNITY HEALTH CENTER</div>
    </div>
    <div class="contact">
      <address class="contact-address" style="font-style:normal">
        PO Box 482 Larkfield<br>Northland 60214
      </address>
      <ul class="contact-lines">
        <li>
          <svg viewBox="0 0 24 24" aria-hidden="true"><path d="M6.6 10.8a15.1 15.1 0 0 0 6.6 6.6l2.2-2.2c.3-.3.7-.4 1-.2 1.1.4 2.3.6 3.6.6.6 0 1 .4 1 1V20c0 .6-.4 1-1 1A17 17 0 0 1 3 4c0-.6.4-1 1-1h3.5c.6 0 1 .4 1 1 0 1.3.2 2.5.6 3.6.1.3 0 .7-.2 1z"/></svg>
          (555) 014.2739
        </li>
        <li>
          <svg viewBox="0 0 24 24" aria-hidden="true"><path d="M2 5h20v14H2z M2 5l10 8 10-8" /><path d="M3 6l9 7 9-7v-1H3z" fill="#fff"/></svg>
          info@vitaridge.com
        </li>
        <li>
          <svg viewBox="0 0 24 24" aria-hidden="true"><circle cx="12" cy="12" r="10"/><path d="M7 7c2 0 3 1 3 3s-2 2-2 4 1 3 0 5M14 4c0 2 2 3 4 3M14 20c0-3 2-4 4-5" stroke="#fff" stroke-width="1.6" fill="none"/></svg>
          www.vitaridge.com
        </li>
      </ul>
    </div>
  </header>

  <section class="letter-body">
    <p class="salutation">Dear Daniel,</p>
    <p>Donec malesuada orci vitae nulla accumsan porta a id massa. Quisque accumsan iaculis magna sit amet fringilla. Maecenas consequat, magna eget tincidunt semper, odio nibh rutrum mi, id feugiat ante nisi eu risus. Vestibulum nunc orci, rhoncus a placerat in, ultricies in mi. Cras mattis varius eros, vel fringilla nisi suscipit eget. Quisque scelerisque sagittis nulla at porttitor.</p>
    <p>Lorem ipsum dolor sit amet, consectetur adipiscing elit. Donec orci purus, luctus vitae dignissim eu, iaculis sed purus. Vivamus faucibus, ipsum nec aliquet viverra, leo mauris condimentum ligula, sit amet sagittis enim ligula quis arcu. Nam egestas tortor id nisi porttitor mattis. In tortor ante, ultricies in suscipit a, tempus non massa. Vivamus et auctor mi. Fusce vel massa nulla. Phasellus nec eros mauris, et scelerisque orci.</p>
    <p class="gap-before">It is a long established fact that a reader will be distracted by the readable content of a page when looking at its layout. The point of using Lorem Ipsum is that it has a more-or-less normal distribution of letters, as opposed to using 'Content here, content here', making it look like readable English. Many desktop publishing packages</p>
    <p>Sed id augue vitae urna euismod commodo aliquet a quam. Pellentesque arcu velit, cursus et malesuada ut, consequat et diam. Nullam erat sem, rhoncus id ullamcorper vitae, rhoncus et arcu. In ultricies ultricies nulla, ut rutrum nisi iaculis at. Donec eu magna a metus ornare faucibus. Fusce aliquet faucibus ultricies. Morbi semper, est id tincidunt gravida, sem arcu adipiscing lacus, ac bibendum nulla leo eu purus. Quisque nec diam sed risus consectetur a ccumsan quis quis nibh. Vestibulum id purus lorem.</p>
    <p class="closing">Sincerely,</p>
  </section>

  <div class="footer-band"></div>
</main>
</body>
</html>
```